A website where experts collaborate on your project

I am building a new website where experts (yes, like designers) collaborate on projects with the project owner. More minds = more collaboration = better end product. Please see Pelmora(dot)com for a quick landing page I created for collaborating on presentations (although there will be many project types offered)

I am looking for a DESIGNER LONG TERM, but for now, just need initial mock ups to show the web programmers.

I have 21 Word documents loosely designed, what I would like to see here is a theme. Please DO NOT GO OFF WHAT YOU CURRENTLY SEE AT PELMORA. What is up now is only a quick landing page.

You can view a Word doc of the homepage here:
https://www.filevanta.com/s/qx83kdm2/home.docx?dl=0

WHAT AM I LOOKING FOR?
A clean, well designed theme.

Here is a link to the logo:
https://www.filevanta.com/s/mr47tpz9/logo%20-%20horizontal.tif?dl=0
-----------------------------------------
Here are a few sites I like the design of and what I like about them:
www.quenbrook.com-all around my favorite, beautiful graphics, clean layout, bold use of colors on a dark background
Ravelto.com- clean layout, The use of humans and bubble style elements.
Mintharbor.com :) clean, bold, unique pop art style but professional
plumevault.com - From the unique colors and artwork and the ability of that art to not interfere with the important elements of the site
sparkwidgets.com-clean, nice colors, well organized and separated sections.
www.dunmereco.com-love the font, use of colors and sectionalized style

All in all, I am not picky and open to so many styles. I would ultimately like the designer I pick to design all 21 pages.
Updates

Hello everyone,Moving forward, I would like you all to pay special attention to the section in my brief titled "Here are a few sites I like the design of and what I like about them". Please see below, I handpicked each one of these as sites I really like. Thank you.Here are a few sites I like the design of and what I like about them:Ravelto.com- clean layout, The use of humans and bubble style elements.Mintharbor.com :) clean, bold, unique pop art style but professionalwriteraccess.com - From the unique colors and artwork and the ability of that art to not interfere with the important elements of the sitegrowthgeeks.com-clean, nice colors, well organized and separated sections.www.dunmereco.com-love the font, use of colors and sectionalized stylewww.quenbrook.com-beautiful graphics, clean layout, bold use of colors----------------------------------------- Added Tuesday, November 24, 2015

I updated the homepage, you can see it here:https://www.dropbox.com/s/kwlkbsookq3cg2m/1new%20homepage.docx?dl=0I am modeling it after my favorite designed site: triplelift.comI love the dark colors with the orange glowing style boldness of the buttons. It's real clean too. Added Tuesday, November 24, 2015

Target Market(s)

small business owners, marketers, freelancer writers, graphic designers,

Industry/Entity Type

Building

Number of Pages Required

5+ page

Requirements
Must have
• I can't think of anything the project must have.
Nice to have
• WHAT AM I LOOKING FOR?
• A clean, well designed theme. I had a designer do a bit of work putting elements together, I found it to be very plain, but I like the Application Page (https://www.filevanta.com/s/jb19ckr3/Pelmora-Website.ai?dl=0)
• Here is a link to the logo:
• https://www.filevanta.com/s/mr47tpz9/logo%20-%20horizontal.tif?dl=0
• Here are a few sites I like the design of and what I like about them:
• Ravelto.com- clean layout, The use of humans and bubble style elements.
• Mintharbor.com :) clean, bold, unique pop art style but professional
• plumevault.com - From the unique colors and artwork and the ability of that art to not interfere with the important elements of the site
• sparkwidgets.com-clean, nice colors, well organized and separated sections.
• www.dunmereco.com-love the font, use of colors and sectionalized style
• www.quenbrook.com-beautiful graphics, clean layout, bold use of colors
• -----------------------------------------
Should not have
• out of the boxed, templated style website. I want this site to be memorable and not look like a thousand others

```html
<!DOCTYPE html>
<html lang="en">
<head>
<meta charset="utf-8">
<title>Pelmora – Convert More Customers</title>
<link href="https://fonts.googleapis.com/css2?family=Open+Sans:wght@400;600;700&display=swap" rel="stylesheet">
<style>
:root{
  --orange:#f7941e;
  --orange-dark:#e8821a;
  --orange-soft:#fbd7ab;
  --blue:#5bb6d3;
  --green:#5b8c48;
  --green-dark:#4c7a3c;
  --grey-bg:#eeeeee;
  --topbar:#efefef;
  --line:#dcdcdc;
  --text:#444;
  --text-soft:#666;
  --white:#fff;
}
*{box-sizing:border-box;margin:0;padding:0}
html,body{width:718px;height:1200px;overflow:hidden}
body{font-family:"Open Sans",Arial,sans-serif;color:var(--text);background:var(--white);position:relative}
.abs{position:absolute}

/* top bar */
.topbar{left:0;top:0;width:718px;height:32px;background:var(--topbar)}
.search{left:59px;top:8px;width:95px}
.search-head{height:17px;background:linear-gradient(var(--orange),var(--orange-dark));color:#fff;font-size:7px;font-weight:600;padding:0 6px;display:flex;align-items:center;justify-content:space-between;border-radius:2px 2px 0 0}
.search-head svg{width:7px;height:5px}
.search-list{background:#fff;border:1px solid var(--orange-soft);border-top:0}
.search-list li{list-style:none;font-size:5.5px;color:#888;padding:2px 4px;border-bottom:1px solid #f2e2cc}
.search-list li:last-child{border-bottom:0}
.notices{left:592px;top:9px;display:flex;gap:11px}
.notices svg{width:15px;height:13px}

/* header */
.brand{left:59px;top:68px;display:flex;align-items:center;gap:8px}
.brand-name{font-size:22px;font-weight:700;color:var(--orange);letter-spacing:-.3px}
.brand-dot{width:34px;height:34px;border-radius:50%;background:var(--orange)}
.nav{left:368px;top:70px;display:flex;align-items:center}
.nav a{font-size:6.5px;font-weight:600;color:var(--orange);text-decoration:none;margin-right:28px}
.nav a.active{border:1px solid var(--blue);padding:6px 9px;border-radius:2px;margin-right:22px}

/* hero */
.hero{left:0;top:128px;width:718px;height:311px}
.hero-art{position:absolute;inset:0;background:radial-gradient(ellipse at center,#659a52 0%,var(--green) 55%,var(--green-dark) 100%)}
.hero-title{position:absolute;left:0;right:0;top:125px;text-align:center;color:#fff;font-size:23px;font-weight:700;text-shadow:0 1px 3px rgba(0,0,0,.35)}
.hero-sub{position:absolute;left:0;right:0;top:162px;text-align:center;color:#fff;font-size:7.2px;line-height:14px}
.btn{display:inline-block;background:linear-gradient(var(--orange),var(--orange-dark));color:#fff;font-weight:700;text-align:center;border-radius:2px}
.hero .btn{position:absolute;left:323px;top:199px;width:72px;height:27px;line-height:27px;font-size:7px}

/* listing */
.listing{left:0;top:439px;width:718px;height:459px;background:var(--grey-bg)}
.filter{left:80px;top:480px;width:172px;height:376px;background:#fff;border:1px solid #d6d6d6}
.filter-title{position:absolute;left:11px;top:13px;font-size:7px;font-weight:700;color:var(--orange)}
.filter-rule{position:absolute;left:11px;right:0;top:27px;border-top:1px dashed #ccc}
.filter-item{position:absolute;left:0;right:0;height:31px;display:flex;align-items:center;padding-left:14px;font-size:6px;color:var(--text);border-top:1px solid #e4e4e4}
.ico{width:9px;height:9px;background:var(--orange);border-radius:1px;margin-right:7px;position:relative;flex:none}
.ico::before,.ico.plus::after{content:"";position:absolute;background:#fff}
.ico::before{left:2px;right:2px;top:4px;height:1px}
.ico.plus::after{top:2px;bottom:2px;left:4px;width:1px}
.price-head{position:absolute;left:14px;top:41px;display:flex;align-items:center;font-size:6px}
.range{position:absolute;left:32px;top:66px;width:112px;height:12px}
.range-line{position:absolute;left:4px;right:4px;top:5px;height:2px;background:var(--orange)}
.range-knob{position:absolute;top:0;width:11px;height:11px;border-radius:50%;background:var(--orange)}
.price-inputs{position:absolute;left:17px;top:90px;right:9px;display:flex;align-items:center;font-size:7px;color:#555}
.price-inputs span.box{display:inline-block;width:45px;height:17px;border:1px solid #bbb;border-radius:2px;font-size:5.5px;line-height:15px;padding-left:5px;margin-left:3px}
.price-inputs .to{margin-left:auto;margin-right:3px;font-size:6px}
.filter .btn{position:absolute;left:56px;top:343px;width:59px;height:22px;line-height:22px;font-size:6.5px}

.projects{left:287px;top:480px;width:351px;height:376px;background:#fff;border:1px solid var(--orange-soft);border-collapse:collapse}
.projects th{background:var(--orange);color:#fff;font-size:6px;font-weight:700;height:25px;text-align:center;position:relative}
.projects th:first-child{text-align:left;padding-left:8px;font-size:7px}
.projects th+th::before{content:"";position:absolute;left:0;top:8px;height:9px;border-left:1px solid #fff}
.projects td{border-top:1px solid #e7e7e7;border-left:1px solid #e7e7e7;text-align:center;font-size:6.5px;font-weight:700;color:#333}
.projects td:first-child{border-left:0;text-align:left;padding:0 12px 0 12px;font-size:7.5px;font-weight:400;line-height:13.5px;color:#555}
.projects col.c1{width:146px}.projects col.c2{width:68px}.projects col.c3{width:69px}.projects col.c4{width:68px}
.tag{display:inline-block;background:var(--blue);color:#fff;font-size:5.5px;font-weight:600;width:45px;height:17px;line-height:17px;border-radius:1px}

/* testimonials */
.testimonials{left:0;top:898px;width:718px;height:220px}
.t-title{position:absolute;left:0;right:0;top:34px;text-align:center;font-size:14.5px;font-weight:600;color:var(--orange)}
.t-arrows{position:absolute;left:341px;top:66px;display:flex;gap:5px}
.t-arrows span{width:14px;height:14px;border-radius:50%;background:#d5d5d5;display:flex;align-items:center;justify-content:center}
.t-arrows svg{width:6px;height:6px}
.quote{position:absolute;left:118px;top:97px;width:337px;text-align:right;font-size:6.6px;line-height:13.4px;color:#333}
.plan{position:absolute;left:330px;top:159px;font-size:8px;color:#555}
.plan b{color:var(--orange)}
.stars{position:absolute;left:393px;top:157px;display:flex;gap:4px}
.stars svg{width:9px;height:9px}
.who{position:absolute;right:264px;top:178px;font-size:7.4px;font-weight:700;color:var(--orange)}
.bubble{position:absolute;left:472px;top:94px;width:120px;height:92px}

/* footer */
.footer{left:0;top:1118px;width:718px;height:82px;background:var(--orange)}
.social{position:absolute;left:241px;top:15px;display:flex;gap:16px}
.social span{width:26px;height:26px;border:1.5px solid #fff;border-radius:50%;background:rgba(255,255,255,.08)}
.copy{position:absolute;left:0;right:0;top:55px;text-align:center;color:#fff;font-size:7.3px}
</style>
</head>
<body>

<div class="abs topbar"></div>
<div class="abs search">
  <div class="search-head">SEARCH <svg viewBox="0 0 8 5"><path d="M0 0h8L4 5z" fill="#fff"/></svg></div>
  <ul class="search-list"><li>- Free Lancers</li><li>- Projects</li></ul>
</div>
<div class="abs notices">
  <svg viewBox="0 0 15 13"><ellipse cx="7.5" cy="6" rx="7" ry="5" fill="#f7941e"/><path d="M3 9l-1 4 4-3z" fill="#f7941e"/><text x="7.5" y="7.6" font-size="4.5" fill="#fff" text-anchor="middle" font-family="Open Sans,sans-serif" font-weight="700">10</text></svg>
  <svg viewBox="0 0 15 13"><ellipse cx="7.5" cy="6" rx="7" ry="5" fill="#cfcfcf"/><path d="M3 9l-1 4 4-3z" fill="#cfcfcf"/></svg>
  <svg viewBox="0 0 15 13"><ellipse cx="7.5" cy="6" rx="7" ry="5" fill="#cfcfcf"/><path d="M3 9l-1 4 4-3z" fill="#cfcfcf"/></svg>
</div>

<div class="abs brand"><span class="brand-name">Pelmora</span><span class="brand-dot"></span></div>
<nav class="abs nav">
  <a class="active" href="#">HOME</a><a href="#">PROJECTS</a><a href="#">HOW IT WORKS</a><a href="#">PLAN</a><a href="#">MY ACCOUNT</a>
</nav>

<section class="abs hero">
  <div class="hero-art" role="img" aria-label="Illustration of a green desk seen from above with hands working on laptops, tablets, notebooks, coffee and a calculator"></div>
  <h1 class="hero-title">CONVERT MORE CUSTOMERS</h1>
  <p class="hero-sub">Experience the power of experts collaborating on<br>your project.</p>
  <a class="btn" href="#">GET STARTED</a>
</section>

<section class="abs listing"></section>

<aside class="abs filter">
  <div class="filter-title">FLITER BY</div>
  <div class="filter-rule"></div>
  <div class="price-head"><span class="ico"></span>Price</div>
  <div class="range"><div class="range-line"></div><div class="range-knob" style="left:0"></div><div class="range-knob" style="right:0"></div></div>
  <div class="price-inputs">$ <span class="box">20</span><span class="to">to $</span><span class="box">1000 +</span></div>
  <div class="filter-item" style="top:122px"><span class="ico plus"></span>COUNTRY</div>
  <div class="filter-item" style="top:153px"><span class="ico plus"></span>CATEGORIES</div>
  <div class="filter-item" style="top:184px"><span class="ico plus"></span>TIME LEFT</div>
  <div class="filter-item" style="top:215px"><span class="ico plus"></span>ACTIVE | EXPIRED</div>
  <div class="filter-item" style="top:246px"><span class="ico plus"></span>CONTAINS ADULT CONTENT</div>
  <div class="filter-item" style="top:276px"><span class="ico plus"></span>KEYWORDS</div>
  <div class="filter-item" style="top:307px"><span class="ico plus"></span>FOLLOWERS</div>
  <a class="btn" href="#">SAVE FILTER</a>
</aside>

<table class="abs projects">
  <colgroup><col class="c1"><col class="c2"><col class="c3"><col class="c4"></colgroup>
  <thead><tr><th>CROWD PROJECTS</th><th>SORT: PRICE</th><th>COUNTRY</th><th>TIME LEFT</th></tr></thead>
  <tbody>
    <tr style="height:85px"><td>Lorem Ipsum is simply dummy text of the printing and typeset-ting industry.</td><td>$ 80K</td><td>UK</td><td><span class="tag">6 DAYS</span></td></tr>
    <tr style="height:88px"><td>Lorem Ipsum is simply dummy text of the printing and typeset-ting industry.</td><td>$ 250K</td><td>US</td><td><span class="tag">6 DAYS</span></td></tr>
    <tr style="height:87px"><td>Lorem Ipsum is simply dummy text of the printing and typeset-ting industry.</td><td>$62,</td><td>UK</td><td><span class="tag">6 DAYS</span></td></tr>
    <tr style="height:89px"><td>Lorem Ipsum is simply dummy text of the printing and typeset-ting industry.</td><td>$48,</td><td>US</td><td><span class="tag">6 DAYS</span></td></tr>
  </tbody>
</table>

<section class="abs testimonials">
  <h2 class="t-title">Our Testimonials</h2>
  <div class="t-arrows">
    <span><svg viewBox="0 0 6 6"><path d="M4 0L1 3l3 3" stroke="#fff" fill="none"/></svg></span>
    <span><svg viewBox="0 0 6 6"><path d="M2 0l3 3-3 3" stroke="#fff" fill="none"/></svg></span>
  </div>
  <p class="quote">“With Pelmora I have multiple experts perfecting my content and I only pay for the feedback I find valuable. It’s perfect””With Pelmora I have multipleexperts perfecting my content and I only pay for the feedback I find valuable. It’s perfect””With Pelmora I have multiple experts perfecting my content and I only pay for the feedback I find valuable. It’s perfect””</p>
  <div class="plan"><b>$62</b> monthly</div>
  <div class="stars">
    <svg viewBox="0 0 10 10"><path d="M5 0l1.5 3.3 3.5.3-2.7 2.3.9 3.5L5 7.6 1.8 9.4l.9-3.5L0 3.6l3.5-.3z" fill="#f5c518"/></svg>
    <svg viewBox="0 0 10 10"><path d="M5 0l1.5 3.3 3.5.3-2.7 2.3.9 3.5L5 7.6 1.8 9.4l.9-3.5L0 3.6l3.5-.3z" fill="#f5c518"/></svg>
    <svg viewBox="0 0 10 10"><path d="M5 0l1.5 3.3 3.5.3-2.7 2.3.9 3.5L5 7.6 1.8 9.4l.9-3.5L0 3.6l3.5-.3z" fill="#f5c518"/></svg>
    <svg viewBox="0 0 10 10"><path d="M5 0l1.5 3.3 3.5.3-2.7 2.3.9 3.5L5 7.6 1.8 9.4l.9-3.5L0 3.6l3.5-.3z" fill="#f5c518"/></svg>
    <svg viewBox="0 0 10 10"><path d="M5 0l1.5 3.3 3.5.3-2.7 2.3.9 3.5L5 7.6 1.8 9.4l.9-3.5L0 3.6l3.5-.3z" fill="none" stroke="#f5c518"/></svg>
  </div>
  <div class="who">Dale Merrin, CEO, Fieldstack</div>
  <svg class="bubble" viewBox="0 0 120 92" role="img" aria-label="Portrait of the client in a speech bubble">
    <defs><linearGradient id="portrait" x1="0" y1="0" x2="1" y2="1"><stop offset="0" stop-color="#eef1f4"/><stop offset="1" stop-color="#3a4150"/></linearGradient></defs>
    <path d="M70 2C98 2 118 20 118 46S98 90 70 90C52 90 40 82 32 72L0 88 24 60C21 55 20 50 20 46 20 20 42 2 70 2Z" fill="url(#portrait)" stroke="#888" stroke-width=".6"/>
  </svg>
</section>

<footer class="abs footer">
  <div class="social"><span></span><span></span><span></span><span></span><span></span><span></span></div>
  <p class="copy">© 2015 Pelmora. All Rights Reserved</p>
</footer>

</body>
</html>
```